IT Company Business Card Design w/Stationary Design

We have a great logo we like! We are looking to redesign our business cards and all company logo'd merchandise/materials.

We are an IT Company located near the Bay Area (San Francisco, CA). We specialize in Managed Services and offer complete IT Computer and Network Support to Businesses of all sizes. We thrive on making a lasting impression. We have been doing IT for 15yrs+ but are young at heart. We like to stand out and be different. We want to be unique and have a recognizable brand. We need our logo to represent who we are. We are young, professional, creative and outstanding. We don't want to blend in, we want to stand out. Our business card needs to stand out and grab attention. Something Bold, yet simple and clean. (I will provide ideas of what we like to give a taste of what we are looking for).

The design can include any kind of texture/artistic design or sizing EXCEPT please "no square card designs" as they don't seem to fit in wallets very well. We dont mind curved edges, rounded corners, vertical layouts or horizontal layouts, embossing, letter press or raised surfaces. Again, we dont want to look average or plain or boring. :) Be creative - yet practical! We have ordered from ZEPLA designs before and been very happy. Their card sizes tend to be a little different, so beware. Hope this helps!

Target Market(s)

Businesses - Small to Medium, Corporations, Publicly Traded Companies

Industry/Entity Type

Business

Contact Information for Business Card

Harbor Lantern IT
7158 Delacroix Avenue
Suite K
Modesto, CA 95871

Office 209.555.0173
Direct 209.555.0148
Cell 209.555.0196

Dale Pruitt
Founder, CEO
www.hlxq.com
dpruitt@hlxq.com

Locations Serviced: Modesto, Stockton, Pleasanton, Fresno (incorporate this on the card ONLY if there's a good place to do so).

What we specialize in: Computer, Network, Voice, Data. (IT Services)

Our Logo Colors: Black and Blue (#006699). Open to using grey or orange as well - but not required. Don't want too busy....

Logo Font: "Cinthe" (Will attach logo font). We want type style to be clean. You can show different font types including our logo font - and we are open to other font ideas.

The logo can be separated. You can use elements together or apart. Surprise us! :) We "REALLY" want the "hl" to be our identifier/our brand people recognize.

Font styles to use
Sans Serif

Colors
0355a3
3176b5
f37122
f78f20
faa54b
474747
aaaaaa
757575
000000

Requirements
Must have
• Bold, Big, Colorful, Modern/yet Fun, Clean Design, Stand Out Presence, Texture would be welcomed - but not necessary, Card design shape can include cut corners or rounded or square edges. Be creative. (HOWEVER, we don't want a square design because we have found it doesn't fit in wallets that easily).
• We do like using ZEPLA printing company (Which they have particular sizing on their card templates - beware), but are open to other design templates/printing companies as well. We just want to make sure its easy to find a print company to do our work. Too unique could be costly and hard to get cards printed.
• Colors to use: Our logo Blue (#006699), with either whites, grays, black, shades of our blue, and maybe a pinch of orange if needed. Primarily, blue, white, gray or black.
Nice to have
• Texture would be cool or little different edging or shape - but nothing too costly to print. I have seen cards with 3 sharp edges and one round edge. Something like that would be cool as an option. Or a vertical card.
• I love a faded watermark look. It would be nice to see some shading of our circle logo on a few designs. The circle with "hl" in it OR.... taking just the "hl" and using it alone.
Should not have
• No square card designs. Nothing too expensive or elaborate to print. No busy fonts. Do not like Times New Roman type fonts (too old looking). Not a lot of orange (if you even choose to use some orange).

```html
<!DOCTYPE html>
<html lang="en">
<head>
<meta charset="utf-8">
<title>Harbor Lantern IT – Business Card</title>
<link rel="stylesheet" href="https://fonts.googleapis.com/css2?family=Exo+2:wght@600&family=Questrial&display=swap">
<style>
  :root {
    --brand-blue: #1f84bf;
    --card-white: #ffffff;
    --stage: #c9c9c9;
    --text-on-blue: #ffffff;
  }
  * { margin: 0; padding: 0; box-sizing: border-box; }
  html, body { width: 1200px; height: 907px; overflow: hidden; }
  body { background: var(--stage); position: relative; font-family: "Questrial", sans-serif; }

  .card { position: absolute; left: 300px; width: 600px; background: var(--card-white); overflow: hidden; }
  .card--front { top: 92px; height: 343px; border-radius: 14px 14px 14px 0; }
  .card--back  { top: 471px; height: 345px; border-radius: 0 14px 0 14px; }

  .front-shape { position: absolute; inset: 0; }

  .contact { position: absolute; left: 32px; top: 40px; color: var(--text-on-blue); }
  .contact__name { font-family: "Exo 2", sans-serif; font-weight: 600; font-size: 19px; letter-spacing: 1.5px; }
  .contact__role { font-family: "Exo 2", sans-serif; font-weight: 600; font-size: 15px; letter-spacing: 1.5px; margin-top: 4px; opacity: .95; }
  .contact__address { margin-top: 24px; font-size: 15px; line-height: 23px; }
  .contact__lines { list-style: none; margin-top: 14px; font-size: 15px; }
  .contact__lines li { display: flex; align-items: center; height: 24px; }
  .contact__lines svg { width: 14px; height: 14px; margin-right: 8px; fill: var(--text-on-blue); }

  .brand-name {
    position: absolute;
    display: flex;
    align-items: center;
    gap: 12px;
    color: var(--brand-blue);
    font-family: "Questrial", sans-serif;
    font-size: 28px;
    line-height: 1;
    white-space: nowrap;
  }
  .brand-name__dot { width: 30px; height: 30px; border-radius: 50%; background: var(--brand-blue); flex: none; }

  .brand-name--front { left: 318px; top: 156px; }
  .brand-name--back { left: 40px; top: 44px; }

  .brand-block { position: absolute; left: 327px; top: 60px; width: 258px; height: 258px; border-radius: 22px; background: var(--brand-blue); }
</style>
</head>
<body>
  <section class="card card--front">
    <svg class="front-shape" viewBox="0 0 600 343" width="600" height="343" aria-hidden="true">
      <rect width="600" height="343" fill="var(--brand-blue)"/>
      <path d="M423 0 H600 V343 H452 C330 343 278 290 278 196 C278 96 340 0 423 0 Z" fill="var(--card-white)"/>
    </svg>

    <div class="contact">
      <p class="contact__name">Dale Pruitt</p>
      <p class="contact__role">Founder, CEO</p>
      <p class="contact__address">Harbor Lantern IT<br>7158 Delacroix Avenue<br>Suite K Modesto, CA 95871</p>
      <ul class="contact__lines">
        <li><svg viewBox="0 0 16 16"><path d="M1 6c0-2 3-3 7-3s7 1 7 3v1h-4V6H5v1H1z M3 8h10l1 6H2z"/></svg>209.555.0173</li>
        <li><svg viewBox="0 0 16 16"><path d="M4 1l3 3-2 2c1 2 3 4 5 5l2-2 3 3-2 3C7 15 1 9 1 3z"/></svg>209.555.0148</li>
        <li><svg viewBox="0 0 16 16"><path d="M4 0h8a1 1 0 0 1 1 1v14a1 1 0 0 1-1 1H4a1 1 0 0 1-1-1V1a1 1 0 0 1 1-1zm1 2v10h6V2z"/></svg>209.555.0196</li>
        <li><svg viewBox="0 0 16 16"><path d="M1 3h14v10H1z M2 4l6 5 6-5" stroke="var(--brand-blue)" stroke-width="1"/></svg>dpruitt@hlxq.com</li>
        <li><svg viewBox="0 0 16 16"><path d="M8 1a7 7 0 1 0 0 14A7 7 0 0 0 8 1zm0 1.5c1 1 1.6 3 1.7 5H6.3c.1-2 .7-4 1.7-5zM2.6 7.5h2.3c.1-2 .5-3.5 1.2-4.7A5.6 5.6 0 0 0 2.6 7.5zm0 1a5.6 5.6 0 0 0 3.5 4.7c-.7-1.2-1.1-2.7-1.2-4.7zm3.7 0c.1 2 .7 4 1.7 5 1-1 1.6-3 1.7-5zm4.8 0c-.1 2-.5 3.5-1.2 4.7a5.6 5.6 0 0 0 3.5-4.7zm2.3-1a5.6 5.6 0 0 0-3.5-4.7c.7 1.2 1.1 2.7 1.2 4.7z"/></svg>www.hlxq.com</li>
      </ul>
    </div>

    <div class="brand-name brand-name--front">
      <span class="brand-name__dot"></span>
      <span>Harbor Lantern</span>
    </div>
  </section>

  <section class="card card--back">
    <div class="brand-name brand-name--back">
      <span>Harbor Lantern</span>
    </div>
    <div class="brand-block"></div>
  </section>
</body>
</html>
```